RWT Fittings Ltd Business Cards

We need a business card with our business logo. We provide window and door installations on high-rises in west coast British Colombia, Canada.

I would like my business information and details on one side of the card, and the other side the company name with logo

Target Market(s)

General Contractors

Industry/Entity Type

Construction

Contact Information for Business Card

one side i want my company name and logo in the dark theme logo that i provided

Requirements
Must have
• Marco Peltieri, 16045518293, RWTFittings@mailbox-demo.com, 1407-5194 Linden Row Burnaby BC, V5H 2K9, Owner & Manager

```html
<!DOCTYPE html>
<html lang="en">
<head>
<meta charset="utf-8">
<title>RWT Fittings Ltd – Business Cards</title>
<link rel="stylesheet" href="https://fonts.googleapis.com/css2?family=Arimo:wght@400;700&display=swap">
<style>
  :root {
    --backdrop: #2b2b2d;
    --card-white: #ffffff;
    --brand-blue: #29a3e0;
    --brand-blue-deep: #2196d3;
    --text-grey: #6e6e6e;
    --mark-grey: #8a8a8a;
    --ink: #3a3a3a;
  }
  * { box-sizing: border-box; margin: 0; padding: 0; }
  html, body { width: 1200px; height: 1108px; overflow: hidden; }
  body {
    background: var(--backdrop);
    font-family: "Arimo", Arial, sans-serif;
    position: relative;
  }
  .card {
    position: absolute;
    top: 187px;
    width: 420px;
    height: 734px;
    border-radius: 28px;
    overflow: hidden;
  }
  .card--front { left: 150px; background: var(--card-white); }
  .card--back { left: 630px; background: var(--brand-blue); }

  .brand {
    display: flex;
    align-items: center;
    justify-content: center;
    gap: 12px;
  }
  .brand__square { width: 34px; height: 34px; flex: none; }
  .brand__name {
    font-weight: 700;
    font-size: 30px;
    letter-spacing: 0.5px;
    line-height: 1.1;
  }
  .card--front .brand { margin-top: 120px; }
  .card--front .brand__square { background: var(--mark-grey); }
  .card--front .brand__name { color: var(--brand-blue); }

  .person { text-align: center; margin-top: 92px; }
  .person__name {
    font-weight: 700;
    font-size: 27px;
    letter-spacing: 1px;
    color: var(--brand-blue);
  }
  .person__name .surname { color: var(--mark-grey); }
  .person__role { font-size: 21px; color: var(--text-grey); margin-top: 4px; }

  .divider-row {
    display: flex;
    align-items: center;
    gap: 8px;
    margin: 18px 40px 0;
  }
  .rule { flex: 1; height: 1.5px; background: var(--brand-blue); }
  .icon {
    width: 30px; height: 30px;
    border-radius: 6px;
    background: var(--brand-blue);
    display: flex; align-items: center; justify-content: center;
  }
  .icon svg { width: 20px; height: 20px; }

  .contact {
    text-align: center;
    font-size: 22px;
    line-height: 1.35;
    color: var(--ink);
    margin-top: 24px;
  }
  .contact .accent { color: var(--brand-blue); }
  .contact-rule { height: 1.5px; background: var(--brand-blue); margin: 22px 40px 0; }
  .address {
    text-align: center;
    font-size: 21px;
    line-height: 1.35;
    color: var(--text-grey);
    margin-top: 20px;
  }

  .back-pattern {
    position: absolute; inset: 0;
    background: linear-gradient(160deg, #33aae3 0%, #269fdc 55%, #2398d5 100%);
  }
  .card--back .brand {
    position: absolute;
    left: 0; right: 0; bottom: 130px;
  }
  .card--back .brand__square { background: var(--card-white); }
  .card--back .brand__name { color: var(--card-white); }
</style>
</head>
<body>
  <section class="card card--front" aria-label="Business card front">
    <div class="brand">
      <span class="brand__square"></span>
      <span class="brand__name">RWT Fittings Ltd</span>
    </div>

    <div class="person">
      <p class="person__name">MARCO <span class="surname">PELTIERI</span></p>
      <p class="person__role">Manager</p>
    </div>

    <div class="divider-row">
      <span class="rule"></span>
      <span class="icon" aria-label="Phone">
        <svg viewBox="0 0 24 24"><path fill="#fff" d="M6.6 10.8a15 15 0 0 0 6.6 6.6l2.2-2.2c.3-.3.7-.4 1-.2 1.1.4 2.3.6 3.6.6.6 0 1 .4 1 1V20c0 .6-.4 1-1 1A17 17 0 0 1 3 4c0-.6.4-1 1-1h3.5c.6 0 1 .4 1 1 0 1.3.2 2.5.6 3.6.1.3 0 .7-.2 1z"/></svg>
      </span>
      <span class="icon" aria-label="Email">
        <svg viewBox="0 0 24 24"><rect x="3" y="6" width="18" height="12" rx="1" fill="#fff"/><path d="M3.5 6.5 12 13l8.5-6.5" fill="none" stroke="#29a3e0" stroke-width="1.6"/></svg>
      </span>
      <span class="icon" aria-label="Website">
        <svg viewBox="0 0 24 24"><circle cx="12" cy="12" r="8.5" fill="none" stroke="#fff" stroke-width="1.8"/><ellipse cx="12" cy="12" rx="3.5" ry="8.5" fill="none" stroke="#fff" stroke-width="1.5"/><path d="M3.5 12h17" stroke="#fff" stroke-width="1.5"/></svg>
      </span>
      <span class="rule"></span>
    </div>

    <div class="contact">
      <p>16045518293</p>
      <p>RWTFittings@mailbox-demo.com</p>
      <p>www.<span class="accent">rwtfittings-demo</span>.com</p>
    </div>
    <div class="contact-rule"></div>
    <div class="address">
      <p>1407-5194 Linden Row</p>
      <p>Burnaby BC, V5H 2K9</p>
    </div>
  </section>

  <section class="card card--back" aria-label="Business card back">
    <div class="back-pattern" role="img" aria-label="Embossed repeating pattern of the company building mark on blue"></div>
    <div class="brand">
      <span class="brand__square"></span>
      <span class="brand__name">RWT Fittings Ltd</span>
    </div>
  </section>
</body>
</html>
```